Business Card Design and Logo Needed

I need Business Cards and a Logo for my website and public speaking business which can be found at: www.corvina-lett.example

I'm looking for creative and unique ideas. Some business cards I've found online that I like can be found at:
http://gigbarrow.example/general/18-smokin-hot-business-card-designs/

and at

http://www.plumquarry.example/2009/04/50-creative-business-cards-of-50-graphic-designers/

```html
<!DOCTYPE html>
<html lang="en">
<head>
<meta charset="utf-8">
<title>Corvina Lett — Business Card</title>
<link rel="stylesheet" href="https://fonts.googleapis.com/css2?family=Italianno&family=Oswald:wght@500;600&display=swap">
<style>
  :root {
    --page: #ffffff;
    --card: #ccb08e;
    --ink: #4a2318;
    --ornament-light: #b8967a;
    --ornament-dark: #8a6450;
  }
  html, body {
    margin: 0;
    width: 1200px;
    height: 900px;
    overflow: hidden;
    background: var(--page);
  }
  .canvas {
    position: relative;
    width: 1200px;
    height: 900px;
  }
  .card {
    position: absolute;
    left: 286px;
    width: 660px;
    height: 368px;
    background: var(--card);
    border-radius: 46px;
    color: var(--ink);
    overflow: hidden;
  }
  .card--front { top: 70px; }
  .card--back { top: 456px; }

  .monogram {
    position: absolute;
    left: 10px;
    top: 18px;
    width: 242px;
    height: 334px;
  }
  .monogram__name {
    position: absolute;
    left: 10px;
    top: 18px;
    width: 242px;
    height: 334px;
    display: flex;
    align-items: center;
    justify-content: center;
    font-family: "Italianno", cursive;
    font-size: 46px;
    color: var(--ink);
    margin: 0;
  }

  .identity {
    position: absolute;
    left: 292px;
    top: 142px;
    width: 320px;
  }
  .identity__name {
    margin: 0;
    font-family: "Italianno", cursive;
    font-weight: 400;
    font-size: 54px;
    line-height: 1;
    letter-spacing: 2px;
  }
  .identity__role {
    margin: 4px 0 0 38px;
    font-family: "Oswald", sans-serif;
    font-weight: 600;
    font-size: 10px;
    letter-spacing: 1px;
    text-transform: uppercase;
  }

  .contact {
    position: absolute;
    left: 258px;
    top: 302px;
    width: 372px;
    margin: 0;
    font-family: "Oswald", sans-serif;
    font-weight: 600;
    font-size: 10px;
    line-height: 18px;
    letter-spacing: 1px;
    text-transform: uppercase;
    text-align: center;
  }
  .contact__line { display: block; }

  .tagline {
    position: absolute;
    left: 0;
    right: 0;
    top: 178px;
    margin: 0;
    text-align: center;
    font-family: "Oswald", sans-serif;
    font-weight: 500;
    font-size: 11px;
    letter-spacing: 4.6px;
    text-transform: uppercase;
  }
</style>
</head>
<body>
<main class="canvas">
  <section class="card card--front" aria-label="Business card front">
    <svg class="monogram" viewBox="0 0 242 334" role="img" aria-label="Flourished swirl ornament framing the brand name">
      <defs>
        <radialGradient id="ornament-tone" cx="50%" cy="50%" r="55%">
          <stop offset="0%" stop-color="var(--ornament-dark)" stop-opacity="0.55"/>
          <stop offset="100%" stop-color="var(--ornament-light)" stop-opacity="0"/>
        </radialGradient>
      </defs>
      <rect x="0" y="0" width="242" height="334" rx="60" fill="url(#ornament-tone)"/>
    </svg>
    <p class="monogram__name">Corvina Lett</p>

    <div class="identity">
      <h1 class="identity__name">Corvina Lett</h1>
      <p class="identity__role">Speaker, Philanthropist, Author</p>
    </div>

    <p class="contact">
      <span class="contact__line">Phone: 555 010 4821 • E-mail: info@corvina-lett.example</span>
      <span class="contact__line">www.corvina-lett.example</span>
    </p>
  </section>

  <section class="card card--back" aria-label="Business card back">
    <p class="tagline">Wonder. Explore. Dream. Achieve.</p>
  </section>
</main>
</body>
</html>
```